Cedarvale Ridge College

We are looking to update our current webpage at www.cedarvaleridge.ca. We would like to make it modern, fresh and appealing to students. We want to keep our logo the same with the logo colours blended in as the primary colours and focus. We are open to reconfiguring content as well.
Reason: Hi, In the next 3 days we will have narrowed our search to 3 designs and will make a choice before the final deadline...
College

```html
<!DOCTYPE html>
<html lang="en">
<head>
<meta charset="utf-8">
<title>Cedarvale Ridge College</title>
<link href="https://fonts.googleapis.com/css2?family=Arvo:wght@400;700&family=Lato:wght@400;700;900&display=swap" rel="stylesheet">
<style>
:root{
  --navy:#13235a;
  --navy-deep:#0d1a45;
  --navy-band:rgba(16,32,88,.88);
  --ink:#222;
  --muted:#555;
  --line:#d8d8d8;
  --paper:#fff;
  --grey-bg:#e8e8e6;
  --footer-black:#0b0b0b;
}
*{box-sizing:border-box;margin:0;padding:0}
html,body{width:1200px;height:2824px;overflow:hidden}
body{position:relative;background:var(--paper);font-family:"Lato",Arial,sans-serif;color:var(--ink)}
.abs{position:absolute}
.serif{font-family:"Arvo",Georgia,serif}
.btn{position:absolute;display:flex;align-items:center;justify-content:center;width:134px;height:38px;border-radius:7px;background:var(--navy);color:#fff;font-weight:700;font-size:15px}

/* header */
.utility{left:617px;top:0;width:447px;height:24px;background:var(--navy-deep);border-radius:0 0 10px 10px;display:flex;align-items:center;justify-content:space-around;padding:0 40px 0 20px;color:#fff;font-size:12px;font-weight:700}
.utility-dot{left:1024px;top:2px;width:20px;height:20px;border:2px solid #fff;border-radius:50%}
.brand{left:134px;top:26px;display:flex;align-items:center;gap:12px}
.brand-mark{width:44px;height:44px;background:var(--navy)}
.brand-name{font-family:"Arvo",Georgia,serif;font-weight:700;font-size:24px;color:var(--navy);line-height:1.1;width:200px}
.search{left:725px;top:56px;width:175px;height:31px;border:1px solid #bbb;background:#fff;font-size:10px;color:#888;padding:9px 8px}
.search-btn{left:872px;top:56px;width:28px;height:31px;background:#9a9a9a}
.socials{left:918px;top:54px;display:flex;gap:7px}
.socials span{width:34px;height:34px;border-radius:50%;background:var(--navy)}
.socials span:last-child{background:#c8322b}

/* nav + hero */
.hero{left:0;top:122px;width:1200px;height:560px;background:linear-gradient(135deg,#2b2b2b,#4a4845 45%,#3a3936 70%,#1f1f1f)}
.nav{left:0;top:122px;width:1200px;height:43px;background:rgba(18,22,40,.9)}
.nav-faint{left:61px;top:136px;font-size:12px;color:#888}
.nav ul{position:absolute;left:134px;top:0;width:936px;height:43px;list-style:none;display:flex;align-items:center;justify-content:space-between;color:#fff;font-size:14px}
.nav li{padding:0 16px;height:43px;display:flex;align-items:center}
.nav li.active{background:var(--navy);font-weight:700}
.hero-band{left:0;top:595px;width:1200px;height:87px;background:var(--navy-band);color:#fff;text-align:center;padding-top:15px}
.hero-band h1{font-size:30px;font-weight:700;letter-spacing:.2px}
.hero-band p{font-size:13px;margin-top:4px}

/* welcome */
.section-title{position:absolute;left:0;width:1200px;text-align:center;font-family:"Arvo",Georgia,serif;font-weight:700;color:var(--navy);font-size:30px}
.rule{position:absolute;height:1px;background:var(--line)}
.welcome-text{left:146px;top:793px;width:908px;text-align:center;font-size:14px;line-height:22px;color:#333}

/* videos */
.videos{left:0;top:995px;width:1200px;height:287px;background:linear-gradient(90deg,#2a1d17,#233127 30%,#2e3e33 55%,#1d2b22 80%,#2a1d17)}
.videos-text{left:150px;top:1087px;width:900px;text-align:center;font-size:14px;line-height:24px;color:#fff}
.play{left:571px;top:1180px;width:58px;height:58px;border:3px solid #fff;border-radius:50%}

/* campus */
.card-img{position:absolute;top:1395px;width:278px;height:182px;border:1px solid var(--line);padding:8px;background:#fff}
.card-img div{width:100%;height:100%}
.card-title{position:absolute;top:1592px;width:278px;text-align:center;font-weight:700;font-size:18px;color:var(--navy)}
.card-text{position:absolute;top:1624px;width:278px;text-align:center;font-size:14px;line-height:22px;color:#333;height:66px;overflow:hidden}

/* admissions + news */
.admit-band{left:0;top:1805px;width:1200px;height:402px;background:linear-gradient(180deg,#ebebea,#dededc)}
.sub-title{position:absolute;top:1860px;font-family:"Arvo",Georgia,serif;font-weight:700;font-size:28px;color:var(--navy)}
.admit-list{left:134px;top:1912px;list-style:none}
.admit-list li{height:35.5px;display:flex;align-items:center;gap:14px;font-size:14px;color:#333}
.tick{width:16px;height:16px;border-radius:50%;background:var(--navy);display:flex;align-items:center;justify-content:center}
.news-img{position:absolute;top:1922px;width:202px;height:96px;background:#fff;padding:7px}
.news-img div{width:100%;height:100%;background:linear-gradient(120deg,#c9d3dc,#8ea2b4 55%,#5d6f83)}
.news-date{position:absolute;top:2042px;font-weight:700;font-size:15px;color:var(--navy)}
.news-text{position:absolute;top:2064px;width:215px;font-weight:700;font-size:15px;line-height:23px;color:#333}
.news-more{position:absolute;top:2131px;font-size:15px;color:var(--navy)}

/* contact */
.contact{left:0;top:2207px;width:1200px;height:581px;background:var(--navy)}
.contact-icon{left:567px;top:2261px;width:66px;height:66px;border:3px solid #fff;border-radius:50%;display:flex;align-items:center;justify-content:center}
.contact-title{left:0;top:2337px;width:1200px;text-align:center;color:#fff;font-size:26px}
.contact-sub{left:0;top:2378px;width:1200px;text-align:center;color:#fff;font-size:14px;line-height:18px}
.col-head{position:absolute;top:2447px;color:#fff;font-family:"Arvo",Georgia,serif;font-size:20px}
.field{position:absolute;left:141px;width:299px;background:#fff;border-radius:6px;font-size:10px;color:#999;padding:10px 12px}
.send{left:141px;top:2694px;width:134px;height:35px;background:#000;border-radius:8px;color:#fff;font-weight:700;font-size:14px;display:flex;align-items:center;justify-content:center}
.map{left:496px;top:2489px;width:320px;height:193px;background:#fff;padding:8px}
.map div{width:100%;height:100%;background:linear-gradient(135deg,#e6e3d8,#d6dccd 50%,#e9e6dc)}
.find{left:870px;width:200px;color:#fff;font-size:13px;line-height:18px;display:flex;gap:12px}
.find svg{flex:none;margin-top:2px}
.find-social{left:870px;top:2662px;display:flex;gap:14px}
.find-social span{width:22px;height:22px;background:#fff;border-radius:2px}
.copyright{left:0;top:2788px;width:1200px;height:36px;background:var(--footer-black);color:#ccc;font-size:12px;display:flex;align-items:center;justify-content:center}
</style>
</head>
<body>

<!-- header -->
<div class="abs utility"><span>Apply Today</span><span>Donate</span><span>Library</span><span>Text For Info</span></div>
<div class="abs utility-dot"></div>
<div class="abs brand"><span class="brand-mark"></span><span class="brand-name">Cedarvale Ridge College</span></div>
<div class="abs search">Search your Subject</div>
<div class="abs search-btn"></div>
<div class="abs socials"><span></span><span></span><span></span><span></span></div>

<!-- hero -->
<div class="abs hero" role="img" aria-label="Student with glasses holding a pen in front of a chalkboard full of formulas and sketches"></div>
<nav class="abs nav">
  <ul>
    <li class="active">Home</li><li>About Us</li><li>Consider Cedarvale</li><li>Current students</li><li>Alumni</li><li>Supporters</li><li>News &amp; Event</li><li>Cedarvale Park</li>
  </ul>
</nav>
<div class="abs nav-faint">Quantity</div>
<div class="abs hero-band">
  <h1>WE WILL HELP YOU TO UNDERSTAND FRIENDLY EDUCATION</h1>
  <p>Lorem ipsum dolor sit amet, consectetuer adipiscing elit, sed diam nonummy nibh euismod tincidunt ut laoreet dolore.</p>
</div>

<!-- welcome -->
<h2 class="section-title" style="top:734px">Welcome Cedarvale Ridge College</h2>
<div class="rule" style="left:530px;top:783px;width:140px"></div>
<p class="abs welcome-text">Lorem ipsum dolor sit amet, consectetur adipiscing elit. Aenean et dignissim sem, interdum risus. Vestibulum consectetur nisi mollis diam pulvinar adipiscing. Vestibulum ut urna nec nibh adipiscing facilisis. Etiam auctor porta lacus ac luctus. Praesent ac libero fermentum, rhoncus magna a, dapibus mauris. Nam ut auctor justo. Sed ante odio, luctus quis nequ nec, adipiscing eleifend arcu. Integer nunc turpis, porttitor at lorem ut. Etiam auctor porta lacus ac luctus. Praesent ac libero fermentum, rhoncus magna.</p>
<div class="btn" style="left:533px;top:901px">Read More</div>

<!-- videos -->
<div class="abs videos" role="img" aria-label="Campus building entrance with the college sign, dimmed"></div>
<h2 class="section-title" style="top:1026px;color:#fff">Cedarvale Videos</h2>
<p class="abs videos-text">Lorem ipsum dolor sit amet, consectetur adipiscing elit. Aenean et dignissim sem, interdum risus. Vestibulum consectetur nisi mollis diam pulvinar adipiscing. Vestibulum ut urna nec nibh adipiscing facilisis. Etiam auctor porta lacus ac luctus. Praesent ac libero fermentum, rhoncus. consectetur adipiscing elit. Aenean et dignissim sem, interdum risus. Vestibulum consectetur nisi mollis diam pulvinar adipiscing.</p>
<div class="abs play"><svg width="52" height="52" viewBox="0 0 52 52"><path d="M20 15 L37 26 L20 37 Z" fill="#fff"/></svg></div>

<!-- campus -->
<h2 class="section-title" style="top:1326px">Our Campus</h2>
<div class="rule" style="left:416px;top:1374px;width:416px"></div>

<div class="card-img" style="left:134px"><div role="img" aria-label="Aerial campus map with location markers" style="background:linear-gradient(135deg,#3b4a7a,#5a6c96 50%,#2c3a64)"></div></div>
<div class="card-title" style="left:134px">Campur Map</div>
<p class="card-text" style="left:134px">Lorem ipsum dolor sit amet, consectetur adipiscing elit. Aenean et dignissim sem, interdum risus. Vestibulum consectetu</p>
<div class="btn" style="left:206px;top:1709px">Read More</div>

<div class="card-img" style="left:461px"><div role="img" aria-label="Street map showing the college location" style="background:linear-gradient(135deg,#e4e2d6,#d3dbc9 50%,#e8e5da)"></div></div>
<div class="card-title" style="left:461px">Map &amp; Directions</div>
<p class="card-text" style="left:461px">Lorem ipsum dolor sit amet, consectetur adipiscing elit. Aenean et dignissim sem, interdum risus. Vestibulum consectetu</p>
<div class="btn" style="left:533px;top:1709px">Read More</div>

<div class="card-img" style="left:786px"><div role="img" aria-label="Auditorium with rows of chairs and a stage" style="background:linear-gradient(180deg,#d9cfc2,#b7a58f 55%,#6b5a4a)"></div></div>
<div class="card-title" style="left:786px">Photo Tour</div>
<p class="card-text" style="left:786px">Lorem ipsum dolor sit amet, consectetur adipiscing elit. Aenean et dignissim sem, interdum risus. Vestibulum consectetu</p>
<div class="btn" style="left:858px;top:1709px">Read More</div>

<!-- admissions + news -->
<div class="abs admit-band" role="img" aria-label="Faint classroom interior behind the admissions and news sections"></div>
<h2 class="sub-title" style="left:134px">Our Admissions</h2>
<ul class="abs admit-list">
  <li><span class="tick"><svg width="10" height="10" viewBox="0 0 10 10"><path d="M2 5 L4 7 L8 3" stroke="#fff" stroke-width="1.6" fill="none"/></svg></span>Download The Full Catalogue</li>
  <li><span class="tick"><svg width="10" height="10" viewBox="0 0 10 10"><path d="M2 5 L4 7 L8 3" stroke="#fff" stroke-width="1.6" fill="none"/></svg></span>Apply Today (Application Package)</li>
  <li><span class="tick"><svg width="10" height="10" viewBox="0 0 10 10"><path d="M2 5 L4 7 L8 3" stroke="#fff" stroke-width="1.6" fill="none"/></svg></span>Information Request</li>
  <li><span class="tick"><svg width="10" height="10" viewBox="0 0 10 10"><path d="M2 5 L4 7 L8 3" stroke="#fff" stroke-width="1.6" fill="none"/></svg></span>Browse our Programs</li>
  <li><span class="tick"><svg width="10" height="10" viewBox="0 0 10 10"><path d="M2 5 L4 7 L8 3" stroke="#fff" stroke-width="1.6" fill="none"/></svg></span>Download Forms</li>
  <li><span class="tick"><svg width="10" height="10" viewBox="0 0 10 10"><path d="M2 5 L4 7 L8 3" stroke="#fff" stroke-width="1.6" fill="none"/></svg></span>Admissions Information</li>
  <li><span class="tick"><svg width="10" height="10" viewBox="0 0 10 10"><path d="M2 5 L4 7 L8 3" stroke="#fff" stroke-width="1.6" fill="none"/></svg></span>Campus Directory</li>
</ul>

<h2 class="sub-title" style="left:605px">News &amp; Event</h2>
<div class="news-img" style="left:607px"><div role="img" aria-label="Students at a campus event"></div></div>
<div class="news-date" style="left:607px">November 22, 2014</div>
<p class="news-text" style="left:607px">Lorem ipsum dolor sit amet consectetur adipiscing elit.</p>
<div class="news-more" style="left:607px">Read More »</div>

<div class="news-img" style="left:866px"><div role="img" aria-label="Students talking outside"></div></div>
<div class="news-date" style="left:866px">November 22, 2014</div>
<p class="news-text" style="left:866px">Lorem ipsum dolor sit amet consectetur adipiscing elit.</p>
<div class="news-more" style="left:866px">Read More »</div>

<!-- contact -->
<div class="abs contact"></div>
<div class="abs contact-icon"><svg width="30" height="22" viewBox="0 0 30 22"><rect x="1" y="1" width="28" height="20" rx="2" fill="#fff"/><path d="M2 2 L15 12 L28 2" stroke="#13235a" stroke-width="2" fill="none"/></svg></div>
<div class="abs contact-title">Contact Us</div>
<p class="abs contact-sub">Please, Feel free to contact anytime. it's always<br>a pleasure meeting new student.</p>
<div class="rule" style="left:445px;top:2428px;width:625px;background:rgba(255,255,255,.35)"></div>

<div class="col-head" style="left:134px">Drop Your Question</div>
<div class="field" style="top:2494px;height:36px">Name</div>
<div class="field" style="top:2546px;height:36px">Email</div>
<div class="field" style="top:2598px;height:78px">Message</div>
<div class="abs send">SEND</div>

<div class="col-head" style="left:496px">Location Map</div>
<div class="abs map"><div role="img" aria-label="Street map with a pin marking the college"></div></div>

<div class="col-head" style="left:870px">Find Us</div>
<div class="abs find" style="top:2489px"><svg width="12" height="16" viewBox="0 0 12 16"><path d="M6 0 C2.7 0 0 2.6 0 5.8 C0 10 6 16 6 16 C6 16 12 10 12 5.8 C12 2.6 9.3 0 6 0 Z" fill="#fff"/><circle cx="6" cy="6" r="2.2" fill="#13235a"/></svg><span>123 euismod cidun ut laoreet laoreet dol magna aliquam PG Fesgalt</span></div>
<div class="abs find" style="top:2562px"><svg width="12" height="14" viewBox="0 0 12 14"><path d="M2 1 L5 1 L6 4 L4 5.5 C5 8 6 9 8.5 10 L10 8 L12 9 L12 12 C8 14 0 7 2 1 Z" fill="#fff"/></svg><span>(123) 456 - 7890</span></div>
<div class="abs find" style="top:2596px"><svg width="12" height="14" viewBox="0 0 12 14"><rect x="1" y="4" width="10" height="8" fill="#fff"/><rect x="3" y="1" width="6" height="4" fill="none" stroke="#fff"/></svg><span>(123) 456 - 7890</span></div>
<div class="abs find" style="top:2627px"><svg width="14" height="10" viewBox="0 0 14 10"><rect width="14" height="10" fill="#fff"/><path d="M0 0 L7 6 L14 0" stroke="#13235a" fill="none"/></svg><span>info@cedarvaleridge.ca</span></div>
<div class="abs find-social"><span></span><span></span><span></span><span></span></div>

<div class="abs copyright">Copyright © 2014 Cedarvaleridge. All Right Reserved</div>

</body>
</html>
```